Natural Light/Organic/Documentary Photography Business

I like a simple, approachable, feminine, earthy/organic feel. Earth/neutral tones, nothing too loud or obnoxious. I like the watercolor look. I don't want anything too trendy or something I'll get tired of after a couple months. As far as colors, I am much more a fan of cream/taupe/blue/green...not a fan of pink or purple at all.

Target Market(s)

Weddings & Families

Industry/Entity Type

Wedding Photography

Contact Information for Business Card

website, email, phone number

Font styles to use
Other font styles liked:
• Horizontes, Gotham

Colors

Designer to choose colors to be used in the design.

Requirements
Must have
• Website: www.mirelhatchway.com
• Phone: 418.629.5073
• Email: mirel@mirelhatchway.com
Nice to have
• I like the watercolor look but its not necessary. I like simple/earthy tones. Nothing too loud or distracting. Simple & feminine without being too girly. I like an approachable/soft feel.
• Instagram: www.instagram.com/mirelhatchwayphotography/
Should not have
• NO loud colors or design or pattern. I do not want a photo of a camera or lens or anything cheesy like that.

```html
<!DOCTYPE html>
<html lang="en">
<head>
<meta charset="utf-8">
<title>Mirel Hatchway Photography – Business Card</title>
<link rel="stylesheet" href="https://fonts.googleapis.com/css2?family=Open+Sans:wght@400;600&display=swap">
<style>
  :root {
    --taupe: #8c7f75;
    --ink: #4a4a4a;
    --card: #ffffff;
    --backdrop: #ececec;
    --band-text: #ffffff;
  }
  * { margin: 0; padding: 0; box-sizing: border-box; }
  html, body { width: 1200px; height: 799px; overflow: hidden; }
  body {
    background: var(--backdrop);
    font-family: "Open Sans", Arial, sans-serif;
    position: relative;
  }
  .card {
    position: absolute;
    left: 313px;
    width: 584px;
    height: 334px;
    background: var(--card);
  }
  .card--front { top: 50px; }
  .card--back { top: 412px; }

  /* Front */
  .contact {
    position: absolute;
    left: 47px;
    top: 176px;
  }
  .contact__name {
    font-size: 20px;
    font-weight: 600;
    color: var(--taupe);
    margin-bottom: 9px;
    letter-spacing: 0.2px;
  }
  .contact__list { list-style: none; }
  .contact__item {
    display: flex;
    align-items: center;
    gap: 8px;
    font-size: 14px;
    line-height: 19px;
    color: var(--ink);
  }
  .contact__icon { width: 13px; height: 13px; flex: none; fill: var(--ink); }
  .monogram {
    position: absolute;
    left: 360px;
    top: 120px;
    width: 190px;
    color: var(--taupe);
    font-size: 34px;
    font-weight: 400;
    line-height: 1.15;
    text-align: center;
  }

  /* Back */
  .wordmark {
    position: absolute;
    left: 0;
    right: 0;
    top: 128px;
    text-align: center;
    color: var(--taupe);
    font-weight: 400;
  }
  .wordmark__name { font-size: 32px; letter-spacing: 1px; line-height: 1.1; }
  .wordmark__tag { font-size: 9px; letter-spacing: 5px; margin-top: 4px; }
  .url-band {
    position: absolute;
    left: 0;
    right: 0;
    top: 277px;
    height: 24px;
    background: var(--taupe);
    color: var(--band-text);
    font-size: 13px;
    font-weight: 600;
    letter-spacing: 4px;
    text-align: center;
    line-height: 24px;
  }
</style>
</head>
<body>
  <section class="card card--front">
    <div class="contact">
      <h1 class="contact__name">Mirel Hatchway</h1>
      <ul class="contact__list">
        <li class="contact__item">
          <svg class="contact__icon" viewBox="0 0 16 16" aria-hidden="true"><path d="M1 5c0-2 3-3 7-3s7 1 7 3v1h-3V5H4v1H1z"/><rect x="2" y="7" width="12" height="8" rx="1"/></svg>
          418.629.5073
        </li>
        <li class="contact__item">
          <svg class="contact__icon" viewBox="0 0 16 16" aria-hidden="true"><rect x="1" y="3" width="14" height="10"/><path d="M1 3l7 6 7-6" fill="none" stroke="#fff" stroke-width="1.3"/></svg>
          mirel@mirelhatchway.com
        </li>
        <li class="contact__item">
          <svg class="contact__icon" viewBox="0 0 16 16" aria-hidden="true"><circle cx="8" cy="8" r="7"/><path d="M1 8h14M8 1c-3 4-3 10 0 14M8 1c3 4 3 10 0 14" fill="none" stroke="#fff" stroke-width="1"/></svg>
          www.mirelhatchway.com
        </li>
        <li class="contact__item">
          <svg class="contact__icon" viewBox="0 0 16 16" aria-hidden="true"><rect x="2" y="2" width="12" height="12" rx="2"/></svg>
          mirelhatchwayphotography
        </li>
      </ul>
    </div>
    <div class="monogram">Mirel<br>Hatchway</div>
  </section>

  <section class="card card--back">
    <div class="wordmark">
      <div class="wordmark__name">Mirel Hatchway</div>
      <div class="wordmark__tag">PHOTOGRAPHY</div>
    </div>
    <div class="url-band">WWW.MIRELHATCHWAY.COM</div>
  </section>
</body>
</html>
```